Flyers

Modify Existing Flyer and create another for exterior company
Updates

Previous Brief has been updated- we want to update this existing one also

Target Market(s)

Exterior Remodeling Customers

Industry/Entity Type

Remodeling/Construction

```html
<!DOCTYPE html>
<html lang="en">
<head>
<meta charset="UTF-8">
<title>Harlow Roofing and Exteriors – Remodeling Flyer</title>
<link href="https://fonts.googleapis.com/css2?family=Montserrat:wght@300;400;500;600;700;800;900&display=swap" rel="stylesheet">
<style>
  :root {
    --blue: #1673c9;
    --orange: #ea5b26;
    --ink: #1c1c1c;
    --panel: #262626;
    --paper: #ffffff;
    --backdrop: #d6d6d6;
    --photo-light: #d9d6d0;
    --photo-mid: #a9a49c;
    --photo-dark: #6d6a66;
  }
  * { box-sizing: border-box; margin: 0; padding: 0; }
  html, body { width: 1200px; height: 960px; overflow: hidden; }
  body {
    background: var(--backdrop);
    font-family: "Montserrat", sans-serif;
    color: var(--ink);
  }
  .flyer {
    position: absolute;
    left: 260px; top: 40px;
    width: 680px; height: 880px;
    background: var(--paper);
    overflow: hidden;
    box-shadow: 0 6px 24px rgba(0,0,0,.18);
  }
  .hero-photo {
    position: absolute; left: 0; top: 0; width: 680px; height: 380px;
    background: linear-gradient(125deg, var(--photo-dark) 0%, var(--photo-mid) 30%, var(--photo-light) 55%, #f1efeb 75%, var(--photo-mid) 100%);
  }
  .brand-panel {
    position: absolute; left: 160px; top: 0; width: 290px; height: 130px;
    background: var(--panel);
    clip-path: polygon(0 0, 100% 0, 92% 100%, 8% 100%);
    display: flex; flex-direction: column; align-items: center; justify-content: center;
  }
  .brand-name {
    color: var(--orange); font-weight: 800; text-transform: uppercase;
    font-size: 32px; letter-spacing: 2px; line-height: 1;
  }
  .brand-sub {
    color: var(--orange); font-weight: 800; text-transform: uppercase;
    font-size: 12px; letter-spacing: 1.5px; margin-top: 8px;
  }
  .headline-tab { position: absolute; left: 0; top: 200px; width: 480px; height: 180px; }
  .headline {
    position: absolute; left: 32px; top: 228px; color: #fff; line-height: 1.1; white-space: nowrap;
  }
  .headline .lead { font-size: 30px; font-weight: 500; display: block; }
  .headline .strong { font-size: 32px; font-weight: 900; display: block; }
  .headline .rest { font-size: 32px; font-weight: 500; display: block; }
  .promise-band {
    position: absolute; left: 0; top: 380px; width: 680px; height: 70px;
    background: var(--orange); color: #fff;
    padding: 11px 32px; line-height: 1.2; white-space: nowrap;
  }
  .promise-band p { font-size: 20px; font-weight: 300; text-transform: uppercase; letter-spacing: .2px; }
  .promise-band strong { font-weight: 800; }
  .services {
    position: absolute; left: 24px; top: 464px; width: 632px;
    display: grid; grid-template-columns: repeat(3, 1fr); gap: 16px;
  }
  .service-head { display: flex; align-items: center; gap: 8px; margin-bottom: 7px; }
  .service-icon {
    width: 34px; height: 34px; border-radius: 50%; background: var(--blue);
    flex: none; display: flex; align-items: center; justify-content: center;
  }
  .service-title {
    color: var(--blue); font-weight: 800; font-size: 16px; line-height: 1; text-transform: uppercase;
  }
  .service-intro { font-size: 11px; font-weight: 700; line-height: 1.3; margin-bottom: 6px; }
  .service-list { list-style: none; }
  .service-list li {
    position: relative; padding-left: 15px; font-size: 10px; line-height: 1.4; font-weight: 500;
  }
  .service-list li::before {
    content: ""; position: absolute; left: 0; top: 3px; width: 10px; height: 10px;
    border-radius: 50%; background: var(--blue);
  }
  .service-list li::after {
    content: ""; position: absolute; left: 3.5px; top: 4.5px; width: 2.5px; height: 4.5px;
    border: solid #fff; border-width: 0 1.5px 1.5px 0; transform: rotate(45deg);
  }
  .service-photo { position: absolute; width: 200px; }
  .photo-kitchen { left: 24px; top: 712px; height: 72px; background: linear-gradient(135deg, var(--photo-mid), #ece8e1 60%, var(--photo-dark)); }
  .photo-bath { left: 240px; top: 664px; height: 120px; background: linear-gradient(135deg, #e9ecef, #c7ccd1 50%, #2b2b2e 85%); }
  .photo-addition { left: 456px; top: 676px; height: 108px; background: linear-gradient(135deg, #f4f3f0, #d8d5cf 55%, #8e9a7c); }
  .web-tab {
    position: absolute; right: 0; top: 784px; width: 200px; height: 28px;
    background: var(--orange); color: #fff; font-weight: 600; font-size: 12.5px;
    display: flex; align-items: center; justify-content: center; white-space: nowrap;
    clip-path: polygon(6% 0, 100% 0, 100% 100%, 0 100%);
  }
  .call-band {
    position: absolute; left: 0; top: 812px; width: 680px; height: 68px;
    background: var(--blue); color: #fff;
    display: flex; align-items: center; padding: 0 24px; gap: 16px; white-space: nowrap;
  }
  .call-text { line-height: 1.05; text-transform: uppercase; }
  .call-text .small { font-size: 14px; font-weight: 400; display: block; }
  .call-text .big { font-size: 22px; font-weight: 800; display: block; }
  .phone-badge {
    width: 46px; height: 46px; border-radius: 50%; background: var(--orange);
    display: flex; align-items: center; justify-content: center; flex: none;
  }
  .phone-number { font-size: 42px; font-weight: 800; letter-spacing: .5px; line-height: 1; }
</style>
</head>
<body>
  <main class="flyer">
    <div class="hero-photo" role="img" aria-label="Photo of a bright white kitchen with granite countertops, stove and windows"></div>

    <div class="brand-panel">
      <span class="brand-name">Harlow</span>
      <span class="brand-sub">Roofing and Exteriors</span>
    </div>

    <svg class="headline-tab" viewBox="0 0 480 180" aria-hidden="true">
      <path d="M0 40 L0 180 L480 180 L480 100 Q480 0 370 0 L110 0 Q40 0 0 40 Z" fill="var(--blue)"/>
    </svg>
    <h1 class="headline">
      <span class="lead">Ready for a</span>
      <span class="strong">Beautiful &amp; Functional</span>
      <span class="rest">Kitchen or Bathroom?</span>
    </h1>

    <div class="promise-band">
      <p>Work with a <strong>Top-Rated Local Remodeling</strong></p>
      <p><strong>Company</strong> in Ankeny, Clive or Urbandale, IA</p>
    </div>

    <section class="services">
      <article class="service">
        <div class="service-head">
          <span class="service-icon"><svg width="20" height="20" viewBox="0 0 20 20" fill="none" stroke="#fff" stroke-width="1.6"><rect x="2" y="8" width="16" height="10"/><line x1="2" y1="12" x2="18" y2="12"/><line x1="6" y1="3" x2="6" y2="8"/></svg></span>
          <h2 class="service-title">Kitchen<br>Remodeling</h2>
        </div>
        <p class="service-intro">Whatever your vision is for your new kitchen, our crew can help you bring it to life. You can trust us for:</p>
        <ul class="service-list">
          <li>Open concept design services</li>
          <li>Kitchen cabinet installation services</li>
          <li>Tile installation services</li>
          <li>Lighting installation services</li>
          <li>Plumbing upgrade services</li>
          <li>Electrical upgrade services</li>
          <li>Drywall services</li>
          <li>Painting services</li>
        </ul>
      </article>
      <article class="service">
        <div class="service-head">
          <span class="service-icon"><svg width="20" height="20" viewBox="0 0 20 20" fill="none" stroke="#fff" stroke-width="1.6"><rect x="3" y="9" width="14" height="8"/><circle cx="7" cy="5" r="2.5"/><line x1="10" y1="13" x2="14" y2="13"/></svg></span>
          <h2 class="service-title">Bathroom<br>Remodeling</h2>
        </div>
        <p class="service-intro">When you hire us for your bathroom remodeling project, the possibilities are endless. Our experienced and talented team can:</p>
        <ul class="service-list">
          <li>Install a custom tile shower</li>
          <li>Build a new vanity</li>
          <li>Install flooring and tile</li>
          <li>Replace your plumbing and light fixtures</li>
        </ul>
      </article>
      <article class="service">
        <div class="service-head">
          <span class="service-icon"><svg width="20" height="20" viewBox="0 0 20 20" fill="none" stroke="#fff" stroke-width="1.6"><path d="M3 10 L10 3 L17 10"/><rect x="5" y="9" width="10" height="8"/></svg></span>
          <h2 class="service-title">Home<br>Additions</h2>
        </div>
        <p class="service-intro">No matter what kind of space you need, our team will bring your vision to life. You can hire us if you need a:</p>
        <ul class="service-list">
          <li>Bathroom addition</li>
          <li>Bedroom addition</li>
          <li>Garage addition</li>
          <li>Basement addition</li>
          <li>Guest room addition</li>
          <li>Living room addition</li>
          <li>Sunroom addition</li>
        </ul>
      </article>
    </section>

    <div class="service-photo photo-kitchen" role="img" aria-label="Photo of a remodeled kitchen counter"></div>
    <div class="service-photo photo-bath" role="img" aria-label="Photo of a modern bathroom with glass shower and dark vanity"></div>
    <div class="service-photo photo-addition" role="img" aria-label="Photo of a bright bedroom addition with large windows"></div>

    <div class="web-tab">www.harlowexteriors.com</div>

    <footer class="call-band">
      <div class="call-text">
        <span class="small">Call today for your</span>
        <span class="big">Free Estimates</span>
      </div>
      <span class="phone-badge"><svg width="22" height="22" viewBox="0 0 24 24" fill="#fff"><path d="M6.6 10.8a15.1 15.1 0 0 0 6.6 6.6l2.2-2.2a1 1 0 0 1 1-.25 11.4 11.4 0 0 0 3.6.57 1 1 0 0 1 1 1V20a1 1 0 0 1-1 1A17 17 0 0 1 3 4a1 1 0 0 1 1-1h3.5a1 1 0 0 1 1 1c0 1.25.2 2.45.57 3.57a1 1 0 0 1-.25 1z"/></svg></span>
      <span class="phone-number">515-555-0142</span>
    </footer>
  </main>
</body>
</html>
```